Vietnam Motorcycle Trip TRAVEL GUIDE!! Book Cover!

I need an adventurous book cover for a book called "THROTTLE MERIDIAN: A Wanderer's Manual for Crossing the Breadth of Vietnam". I would like people to look at the cover and think adventure and Vietnam. I want it to appeal to backpackers and people who have not travelled to Vietnam. A motorbike riding along a road in Vietnam would be ideal with some landscapes to suggest we are definitely in Vietnam. The rear cover could perhaps be one of Vietnam's tropical beaches or something else that says "this place is a paradise". It could also be something else that is quinessentially Vietnamese.

The book will be A5 Dimensions. And it will also need a printable A5 interior cover too. The interior covers can just be images. No text needed. These interior images can be motorcycle related or Vietnam related. Perhaps some images of Vietnam or some Pho or Banh Mi to give it a bit of flavour. Or a long open road with a motorbike on it.

Please leave space in the external rear, lower right hand corner for a barcode.

I've attached some images to gain inspiration from. And a sample chapter.

Colours I'd like to see on there - greens, camoflague perhaps, yellow, brown, blue.

Target Market(s)

Male backpackers aged 18-35 years old. New Zealand and Australian travellers.

Font styles to use
Serif
Sans Serif

Requirements
Must have
• Exterior and Interior covers.
Barcode space.
Title and subtitle.
Synopsis on rear cover.
Exciting title fonts - perhaps Brushstroke or something equally exciting and rugged
Nice to have
• Colours I'd like to see on there - greens, camoflague perhaps, yellow, brown, blue.

A motorbike riding on the open road of Vietnam.

Rice paddies, beaches, Korvan Conflict stuff perhaps.

A New Zealand Flag
A Vietnam Flag
Should not have
• Scenery from countries outside Southeast Asia

```html
<!DOCTYPE html>
<html lang="en">
<head>
<meta charset="utf-8">
<title>Throttle Meridian – Cover Spread</title>
<link rel="stylesheet" href="https://fonts.googleapis.com/css2?family=Roboto+Condensed:wght@400;700&family=PT+Sans:ital,wght@0,400;1,700&display=swap">
<style>
  :root{
    --page:#ffffff;
    --sky-top:#2f7fb8;
    --sky-mid:#4f97c9;
    --sky-light:#8dbde0;
    --cloud:#eef4f6;
    --mountain-haze:#6f8fa3;
    --jungle:#5e8f2c;
    --jungle-bright:#8fb33f;
    --jungle-deep:#25401a;
    --road:#9a9a92;
    --panel:rgba(25,33,42,.9);
    --ink-light:#f1f3f4;
    --title-yellow:#f7d708;
    --barcode:#ffffff;
  }
  *{margin:0;padding:0;box-sizing:border-box}
  html,body{width:745px;height:1200px;overflow:hidden;background:var(--page)}
  .canvas{position:relative;width:745px;height:1200px}
  .spread{position:absolute;left:0;top:330px;width:745px;height:540px;overflow:hidden}

  .cover-photo{
    position:absolute;inset:0;
    background:
      /* light glow spilling down from the top of the front */
      radial-gradient(ellipse 120px 260px at 400px 0px, rgba(255,255,255,.45), transparent 70%),
      linear-gradient(160deg, transparent 52%, rgba(255,255,255,.16) 58%, transparent 64%),
      linear-gradient(172deg, transparent 55%, rgba(255,255,255,.12) 60%, transparent 66%),
      /* clouds, right of centre */
      radial-gradient(ellipse 110px 45px at 660px 255px, var(--cloud) 0%, rgba(238,244,246,.6) 45%, transparent 75%),
      radial-gradient(ellipse 70px 30px at 560px 300px, rgba(238,244,246,.75), transparent 75%),
      radial-gradient(ellipse 60px 22px at 740px 220px, rgba(238,244,246,.7), transparent 75%),
      /* green hillside rising on the right */
      radial-gradient(ellipse 140px 220px at 745px 430px, var(--jungle) 0%, rgba(94,143,44,.85) 55%, transparent 78%),
      /* road sweeping through the lower front */
      radial-gradient(ellipse 150px 40px at 650px 430px, rgba(154,154,146,.85), transparent 75%),
      /* bright jungle foreground on the front */
      radial-gradient(ellipse 210px 120px at 520px 470px, var(--jungle-bright), rgba(94,143,44,.7) 55%, transparent 80%),
      /* hazy mountains on the back */
      radial-gradient(ellipse 260px 70px at 120px 360px, rgba(111,143,163,.9), transparent 75%),
      /* dark jungle along the bottom */
      linear-gradient(180deg, transparent 0%, transparent 72%, rgba(37,64,26,.55) 86%, var(--jungle-deep) 100%),
      linear-gradient(180deg, var(--sky-top) 0%, var(--sky-mid) 30%, var(--sky-light) 52%, var(--jungle) 76%, var(--jungle-deep) 100%);
  }

  .back-panel{
    position:absolute;left:17px;top:0;width:309px;height:487px;
    background:var(--panel);color:var(--ink-light);
    font-family:"PT Sans",sans-serif;font-size:10.4px;line-height:10.9px;
    padding:24px 14px 0 20px;
  }
  .back-headline{font-style:italic;font-weight:700;font-size:14px;line-height:15.6px;margin-bottom:9px}
  .back-panel p{text-align:justify;margin-bottom:10.9px}
  .reveal-list{list-style:none;margin:0 0 8px}
  .reveal-list li{padding-left:8px;text-indent:-8px;width:268px}
  .divider{text-align:center;margin:2px 0 10px}
  .back-panel p.author-bio{font-size:9.4px;line-height:10.9px;letter-spacing:-.15px;margin:0}
  .author-bio b{font-style:italic}
  .barcode-space{position:absolute;left:209px;top:453px;width:102px;height:56px;background:var(--barcode)}

  .spine-title,.spine-author{
    position:absolute;writing-mode:vertical-rl;
    font-family:"Roboto Condensed",sans-serif;color:var(--ink-light)
  }
  .spine-title{left:360px;top:101px;font-size:22.5px;line-height:1;letter-spacing:.4px}
  .spine-title .accent{color:var(--title-yellow)}
  .spine-author{left:366px;top:425px;font-size:7px;line-height:1;letter-spacing:3px;font-weight:700}

  .front-title{position:absolute;left:400px;width:340px;text-align:center;font-family:"Roboto Condensed",sans-serif}
  .title-top{top:32px;font-size:52px;font-weight:400;color:var(--ink-light);line-height:1;letter-spacing:-.3px}
  .title-main{top:75px;font-size:76px;font-weight:700;color:var(--title-yellow);line-height:1;letter-spacing:-.5px}
  .subtitle{top:152px;font-size:18px;font-weight:400;color:var(--ink-light);line-height:24px}
  .front-author{
    position:absolute;left:420px;width:325px;top:495px;text-align:center;
    font-family:"Roboto Condensed",sans-serif;font-size:23px;line-height:1;letter-spacing:5px;color:var(--ink-light)
  }
</style>
</head>
<body>
<main class="canvas">
  <section class="spread">
    <div class="cover-photo" role="img" aria-label="Photo of a rider on a motorbike on a winding mountain road through green jungle, hazy mountains behind, under a blue sky with sun rays and clouds"></div>

    <div class="back-panel">
      <h2 class="back-headline">Travel like a pro in a country<br>where bribing cops is normal!</h2>
      <p>Everyone knows someone who’s ridden the length of Vietnam. What if you could do the same?</p>
      <p>For us Kiwis and Australians, it’s difficult finding decent material about motorcycling in Vietnam. With so much conflicting information online and uncertainty around costs, it’s no wonder people keep putting off this 1600 km road trip.</p>
      <p>Cal Westbury has been there and done it. In the flesh. And whether your goal is riding from Saigon to Hanoi, across multiple Southeast Asian countries, or just hooning around for a few days, this guide is your bulletproof vest.<br>It reveals…</p>
      <ul class="reveal-list">
        <li>&gt; How to plan your own motorcycle odyssey before leaving home</li>
        <li>&gt; Where and how to buy / rent a bike</li>
        <li>&gt; What types of licences and insurance you’ll need</li>
        <li>&gt; How to finish your trip alive without getting shaken down by dodgy cops or run over by a pig truck</li>
        <li>&gt; Itemized expense reports, showing this journey is possible for as little as $90 NZD per day and even as low as $50.</li>
        <li>&gt; A day-by-day outline of our riding itinerary</li>
      </ul>
      <p>None of us are getting any younger. And with all the information you need in one lightweight book, what’s stopping you?</p>
      <div class="divider">***</div>
      <p class="author-bio"><b>Callum Westbury</b> has ridden motorbikes since he was a young chap growing up in the wilds of New Zealand. He has lived in four countries and has an honours degree in Anthropology and History. Callum is also the author of The Riverton Floods: Notes of a Student and is always planning the next motorcycle odyssey.</p>
    </div>
    <div class="barcode-space" aria-label="Barcode space"></div>

    <div class="spine-title">THROTTLE <span class="accent">MERIDIAN</span></div>
    <div class="spine-author">CALLUM WESTBURY</div>

    <h1 class="front-title title-top">THROTTLE</h1>
    <div class="front-title title-main">MERIDIAN</div>
    <div class="front-title subtitle">A WANDERER'S MANUAL FOR CROSSING<br>THE BREADTH OF VIETNAM</div>
    <div class="front-author">CALLUM WESTBURY</div>
  </section>
</main>
</body>
</html>
```